Business Card - connecting 2 souls and beggining the journey of self discovery

Logo on the front
with tag line

On the back list of services and contact details

Seminars
workshops
Coaching
podcasts

Darren Whitlow
Health & Wellbeing Life Coach
0491 372 615
darren@brightcoreliving.example
brightcoreliving.example

Industry/Entity Type

Life Coaching

Contact Information for Business Card

I like the use of colour from the logo to be used. I'm not a fan of white.

Requirements
Must have
• My tagline: The journey home starts with you
Nice to have
• Use of colour that is in the mind body soul logo

```html
<!DOCTYPE html>
<html lang="en">
<head>
<meta charset="utf-8">
<title>Brightcore Living – Business Card</title>
<link rel="stylesheet" href="https://fonts.googleapis.com/css2?family=Montserrat:wght@500&family=Open+Sans:wght@400;600&family=Roboto+Condensed:wght@700&display=swap">
<style>
  :root {
    --bg: #2a2a2b;
    --card-white: #f2f2f2;
    --card-grey: #7f7f82;
    --strip-grey: #7a7a7c;
    --text-grey: #7b7b7d;
    --rule: #c9c9c9;
    --green: #5bb888;
    --pink: #ee5e73;
    --purple: #8d3fc9;
    --orange: #f3a03a;
    --teal: #3bb1a6;
    --lime: #8cc853;
    --white: #ffffff;
    --ink: #4a4a4a;
  }
  * { box-sizing: border-box; margin: 0; padding: 0; }
  html, body { width: 1200px; height: 960px; overflow: hidden; }
  body { background: var(--bg); position: relative; font-family: "Open Sans", sans-serif; }

  .card {
    position: absolute;
    width: 600px;
    height: 342px;
    border-radius: 20px;
    overflow: hidden;
  }
  .card--front { left: 314px; top: 114px; background: var(--card-white); }
  .card--back { left: 311px; top: 472px; background: var(--card-grey); }

  /* front */
  .brand-mark {
    position: absolute; left: 419px; top: 31px;
    width: 78px; height: 78px; border-radius: 50%;
    background: var(--orange);
  }
  .brand-name {
    position: absolute; right: 34px; top: 124px;
    font-family: "Montserrat", sans-serif; font-weight: 500;
    font-size: 20px; letter-spacing: -0.4px; color: var(--text-grey);
  }
  .tagline {
    position: absolute; right: 34px; top: 148px;
    font-weight: 600; font-size: 13px; color: var(--text-grey);
  }
  .person-name {
    position: absolute; left: 33px; top: 193px;
    font-family: "Roboto Condensed", sans-serif; font-weight: 700;
    font-size: 22px; color: var(--green); text-transform: uppercase;
  }
  .person-role {
    position: absolute; left: 33px; top: 219px;
    font-weight: 600; font-size: 14.5px; color: var(--pink);
    text-transform: uppercase; letter-spacing: 0.2px;
  }
  .divider {
    position: absolute; left: 33px; top: 243px;
    width: 533px; height: 1px; background: var(--rule);
  }
  .contact-list { position: absolute; left: 33px; top: 250px; list-style: none; }
  .contact-list li {
    display: flex; align-items: center; gap: 8px;
    height: 19.5px; font-size: 14px; color: var(--ink);
  }
  .contact-list svg { width: 13px; height: 13px; fill: var(--green); }
  .front-strip { position: absolute; left: 0; bottom: 0; width: 600px; height: 13px; }

  /* back */
  .brand-mark--large {
    position: absolute; left: 12px; top: 12px;
    width: 318px; height: 318px; border-radius: 50%;
    background: var(--orange);
  }
  .back-brand-name {
    position: absolute; left: 350px; width: 230px; top: 248px; text-align: center;
    font-family: "Montserrat", sans-serif; font-weight: 500;
    font-size: 19px; letter-spacing: -0.4px; color: var(--white);
  }
  .services {
    position: absolute; left: 350px; width: 230px; top: 277px; text-align: center;
    font-size: 14px; line-height: 18px; color: var(--white);
  }
  .services .dot { font-size: 10px; margin: 0 2px 0 5px; }
</style>
</head>
<body>

<section class="card card--front" aria-label="Business card front">
  <div class="brand-mark" aria-hidden="true"></div>
  <p class="brand-name">Brightcore Living</p>
  <p class="tagline">The journey home starts with you</p>

  <h1 class="person-name">Darren Whitlow</h1>
  <p class="person-role">Health &amp; Wellbeing Life Coach</p>
  <div class="divider"></div>

  <ul class="contact-list">
    <li>
      <svg viewBox="0 0 24 24" aria-hidden="true"><path d="M6.6 10.8a15.1 15.1 0 0 0 6.6 6.6l2.2-2.2c.3-.3.7-.4 1-.2 1.1.4 2.3.6 3.6.6.6 0 1 .4 1 1V20c0 .6-.4 1-1 1A17 17 0 0 1 3 4c0-.6.4-1 1-1h3.5c.6 0 1 .4 1 1 0 1.3.2 2.5.6 3.6.1.3 0 .7-.2 1z"/></svg>
      <span>0491 372 615</span>
    </li>
    <li>
      <svg viewBox="0 0 24 24" aria-hidden="true"><path d="M2 5h20v14H2z M2 5l10 7 10-7" /><path d="M3 6l9 6.3L21 6v1.4l-9 6.3-9-6.3z" fill="#f2f2f2"/></svg>
      <span>darren@brightcoreliving.example</span>
    </li>
    <li>
      <svg viewBox="0 0 24 24" aria-hidden="true"><circle cx="12" cy="12" r="10"/><path d="M7 6c2 1 3 3 2 5s1 3 0 5M15 4c-1 2 1 3 3 4s1 4 0 6" stroke="#f2f2f2" stroke-width="1.6" fill="none"/></svg>
      <span>brightcoreliving.example</span>
    </li>
  </ul>

  <svg class="front-strip" viewBox="0 0 600 13" aria-hidden="true">
    <rect width="600" height="13" fill="var(--strip-grey)"/>
    <polygon points="376,13 389,0 410,0 397,13" fill="var(--purple)"/>
    <polygon points="397,13 410,0 432,0 419,13" fill="var(--pink)"/>
    <polygon points="419,13 432,0 454,0 441,13" fill="var(--orange)"/>
    <polygon points="441,13 454,0 476,0 463,13" fill="var(--pink)"/>
    <polygon points="463,13 476,0 498,0 485,13" fill="var(--orange)"/>
    <polygon points="485,13 498,0 520,0 507,13" fill="var(--teal)"/>
    <polygon points="507,13 520,0 548,0 535,13" fill="var(--lime)"/>
  </svg>
</section>

<section class="card card--back" aria-label="Business card back">
  <div class="brand-mark--large" aria-hidden="true"></div>
  <p class="back-brand-name">Brightcore Living</p>
  <p class="services">
    Seminars<span class="dot">●</span>Workshops<br>
    Coaching<span class="dot">●</span>Podcasts
  </p>
</section>

</body>
</html>
```